Need Business Card ASAP

We need a business card design for a meeting coming up in a few days. The company name is Harlow Ridge Building and Construction and the logo is attached. Something clean, cool, and contemporary that we can get to a printer right away. Attached is the business card for Volmar Energy, an affiliated company, which we like. Instead of the hawk on the back, you could use the attached "D". We'll also be needing matching letterhead in the near future, so ideas for that are welcome.

```html
<!DOCTYPE html>
<html lang="en">
<head>
<meta charset="utf-8">
<title>Harlow Ridge Building and Construction – Business Card</title>
<link rel="stylesheet" href="https://fonts.googleapis.com/css2?family=Source+Sans+3:wght@400;600;700&display=swap">
<style>
  :root {
    --bg: #e8e4dc;
    --card-white: #ffffff;
    --ink: #4d4b48;
    --gold: #b3ab74;
    --gold-light: #e6e2c9;
    --charcoal: #2b2726;
    --black: #1e1c1b;
    --rule: #c9c7c2;
  }
  * { margin: 0; padding: 0; box-sizing: border-box; }
  html, body { width: 1099px; height: 1200px; overflow: hidden; }
  body {
    background: var(--bg);
    font-family: "Source Sans 3", Arial, sans-serif;
    position: relative;
  }
  .card {
    position: absolute;
    width: 838px;
    height: 476px;
    border-radius: 24px;
    overflow: hidden;
    box-shadow: 0 6px 18px rgba(0,0,0,.25);
  }
  /* front */
  .card--front { left: 133px; top: 61px; background: var(--card-white); }
  .brand-block {
    position: absolute; left: 86px; top: 42px; width: 242px; height: 310px;
  }
  .brand-block__square {
    height: 192px;
    background: linear-gradient(135deg, var(--gold) 0%, var(--gold-light) 100%);
  }
  .brand-block__name {
    height: 118px;
    background: var(--black);
    color: var(--gold);
    font-weight: 600;
    font-size: 21px;
    line-height: 1.15;
    text-align: center;
    display: flex; align-items: center; justify-content: center;
    padding: 0 14px;
    letter-spacing: .5px;
  }
  .divider {
    position: absolute; left: 368px; top: 48px; width: 2px; height: 298px;
    background: linear-gradient(to bottom, transparent, var(--rule) 20%, var(--rule) 80%, transparent);
  }
  .contact { position: absolute; left: 397px; top: 64px; color: var(--ink); }
  .contact__name { font-size: 30px; font-weight: 700; color: var(--gold); line-height: 1.2; }
  .contact__title { font-size: 21px; margin-top: 6px; }
  .contact__address { font-size: 21px; line-height: 27px; margin-top: 34px; }
  .contact__lines { list-style: none; margin-top: 30px; font-size: 21px; }
  .contact__lines li { display: flex; align-items: center; height: 35px; }
  .contact__lines svg { width: 16px; height: 16px; margin-right: 10px; fill: var(--gold); }
  .front-band { position: absolute; left: 0; bottom: 0; width: 838px; height: 66px; }
  .front-url {
    position: absolute; right: 36px; bottom: 22px;
    font-size: 20px; font-weight: 700; letter-spacing: 1.6px; color: var(--ink);
  }
  /* back */
  .card--back { left: 120px; top: 605px; background: var(--charcoal); }
  .back-mark {
    position: absolute; left: 0; right: 0; top: 150px;
    display: flex; flex-direction: column; align-items: center; gap: 22px;
  }
  .back-mark__square { width: 56px; height: 56px; background: var(--gold); }
  .back-mark__name { color: #ffffff; font-size: 40px; font-weight: 600; letter-spacing: 1px; }
  .back-url {
    position: absolute; left: 0; right: 0; top: 422px; text-align: center;
    color: #ffffff; font-size: 21px; font-weight: 700; letter-spacing: 1.8px;
  }
</style>
</head>
<body>

<section class="card card--front" aria-label="Business card front">
  <div class="brand-block">
    <div class="brand-block__square"></div>
    <div class="brand-block__name">Harlow Ridge Building &amp; Construction</div>
  </div>
  <div class="divider"></div>
  <div class="contact">
    <p class="contact__name">Graham T. Harlow</p>
    <p class="contact__title">Chief Executive Officer</p>
    <p class="contact__address">2216 West 41st Street<br>Austin, TX 78756</p>
    <ul class="contact__lines">
      <li><svg viewBox="0 0 16 16" aria-hidden="true"><path d="M3 1l3 3-1.5 2a9 9 0 0 0 5.5 5.5L12 10l3 3-2 2C7 15 1 9 1 3z"/></svg>512-555-0148</li>
      <li><svg viewBox="0 0 16 16" aria-hidden="true"><path d="M4 3h8l2 5v5h-2v-2H4v2H2V8zm1 1.5L4 7h8l-1-2.5z"/></svg>512-555-0173</li>
      <li><svg viewBox="0 0 16 16" aria-hidden="true"><path d="M1 4h14v9H1zm1.5 1.2v.3L8 9l5.5-3.5v-.3z"/></svg>graham@harlowridgebuild.com</li>
    </ul>
  </div>
  <svg class="front-band" viewBox="0 0 838 66" preserveAspectRatio="none" aria-hidden="true">
    <defs>
      <linearGradient id="band-gold" x1="0" x2="1">
        <stop offset="0" stop-color="#f3f1e6"/>
        <stop offset="1" stop-color="#bdb67f"/>
      </linearGradient>
    </defs>
    <rect x="0" y="0" width="838" height="66" fill="#f4f3f0"/>
    <polygon points="0,0 372,0 350,22 0,22" fill="#1e1c1b"/>
    <polygon points="384,0 838,0 838,66 0,66 0,42 344,42" fill="url(#band-gold)"/>
  </svg>
  <p class="front-url">www.harlowridgebuild.com</p>
</section>

<section class="card card--back" aria-label="Business card back">
  <div class="back-mark">
    <div class="back-mark__square"></div>
    <p class="back-mark__name">Harlow Ridge</p>
  </div>
  <p class="back-url">www.harlowridgebuild.com</p>
</section>

</body>
</html>
```